Professional Engineering Web Design

Project Brief: Website Redesign for Mechanical Design Consultancy
Project Overview
I want to update and improve my current website to create a more professional, modern, and high-credibility online presence for my mechanical design consultancy.

Current site: https://valtorix.design/

The new website must communicate expertise, precision, and trust—matching the standard of top engineering and product design agencies.

Reference Websites (Style + Structure Inspiration)
These represent the quality, cleanliness, and professionalism I want to achieve:

https://plinthwaredesign.com/
https://www.sorvane.com/
https://bramlow-uk.com/
Brand Look
Professional, modern, engineering-focused aesthetic
Clean layouts and strong typography
High-quality imagery conveying precision, innovation, and mechanical expertise
Colour scheme and styling must follow my existing logo (attached in project)
Platform Requirements
The website must be built on WordPress
Should use a clean, flexible theme or modern page builder (Elementor, Gutenberg, Bricks, or similar)
Avoid overly complex custom coding so I can easily edit content later
Final deliverable must allow me to manage and update content without developer assistance
Functionality
Fast-loading, lightweight, and smooth user experience
Clean animations and transitions similar to the reference sites
Fully mobile responsive
Clear navigation and strong visual hierarchy
Contact forms optimised for lead generation
Optional: subtle scroll effects, case study sliders, icon animations, etc.
SEO Aspirations
Developer should recommend and implement a modern SEO strategy
Proper on-page SEO setup (titles, meta, schema, alt tags, heading structure)
Optimised site architecture for ranking and crawling
Aim: Generate leads through improved visibility and keyword targeting
Optional but useful: Google Analytics, Google Search Console setup
User Journeys
(Recommended structure)

The site should be crafted around clear, intuitive journeys for each type of visitor:

Potential new clients
Quickly understand what services I offer
View examples of past work / case studies
See credibility indicators (process, expertise, industries served)
Easily contact me or request a project discussion
Returning clients
Access updated portfolio items
Find contact details or book follow-up work easily
General visitors discovering through SEO
Be guided to core service areas
Understand my value proposition quickly
Be invited to learn more or make contact
The developer should design the structure to support these journeys smoothly.

Maintenance Expectations
Website will be maintained by me, so it should be easy to update using relatively basic WordPress skills
Use modular templates and simple backend structure
Avoid unnecessary plugins
Provide brief handover documentation if required
Hosting Preferences
Site is currently hosted via a family member
Open to discussing moving to a paid, reliable hosting provider if preferable for performance and maintainability
Developer may advise on the best hosting setup for WordPress
Content
Most content can be taken from the existing website
Developer is welcome to suggest improvements to structure, layout, and imagery
Must remain easy for me to edit or add new content later (e.g., new projects)
Deliverables
Fully built WordPress website
Clean, professional, modern design inspired by the reference sites
Mobile-responsive across all devices
SEO-ready structure and optimisations
Transfer of website and admin rights
Any design assets, templates, or documentation used

```html
<!DOCTYPE html>
<html lang="en">
<head>
<meta charset="utf-8">
<title>Valtorix Mechanical Design</title>
<link href="https://fonts.googleapis.com/css2?family=Montserrat:wght@600;700&family=Lato:wght@400;700&display=swap" rel="stylesheet">
<style>
:root{
  --blue:#2f5be6;
  --blue-dark:#2449c4;
  --ink:#2b2b2b;
  --text:#444;
  --muted:#666;
  --band:#eef1f8;
  --footer:#3b3b3b;
  --white:#fff;
}
*{box-sizing:border-box;margin:0;padding:0}
html,body{width:1200px;height:4128px;overflow:hidden}
body{position:relative;background:var(--white);font-family:'Lato',sans-serif;color:var(--text)}
.abs{position:absolute}
.heading{font-family:'Montserrat',sans-serif;font-weight:700;color:var(--ink)}
.heading .accent{color:var(--blue)}
.btn{position:absolute;display:flex;align-items:center;justify-content:center;background:var(--blue);color:var(--white);border-radius:30px;font-family:'Lato',sans-serif;font-weight:700;font-size:17px}

/* header */
.topbar{left:423px;top:0;width:679px;height:32px;background:var(--blue);border-radius:0 0 16px 16px;color:var(--white);font-size:14px;display:flex;align-items:center}
.topbar .item{position:absolute;display:flex;align-items:center;gap:10px}
.social-dot{width:20px;height:20px;border-radius:50%;border:2px solid currentColor}
.brand{display:flex;align-items:center;gap:14px}
.brand .mark{width:84px;height:84px;border-radius:50%;border:14px solid var(--blue)}
.brand .name{font-family:'Lato',sans-serif;font-weight:700;font-size:40px;color:var(--blue);letter-spacing:1px}
.nav{top:60px;left:603px;display:flex;gap:34px;font-size:16px;color:var(--ink)}

/* hero */
.hero-title{left:0;width:1200px;top:398px;text-align:center;font-family:'Montserrat',sans-serif;font-weight:700;font-size:54px;line-height:64px;color:var(--white);text-shadow:0 2px 8px rgba(0,0,0,.35)}
.hero-sub{left:0;width:1200px;top:556px;text-align:center;font-weight:700;font-size:17px;color:var(--white);text-shadow:0 1px 4px rgba(0,0,0,.5)}

/* about */
.about-text{left:644px;top:888px;width:442px;font-size:14.5px;line-height:25.6px;text-align:justify;color:var(--text)}

/* expertise */
.band{left:0;top:1222px;width:1200px;height:640px;background:var(--band)}
.section-title{left:0;width:1200px;text-align:center;font-size:40px}
.intro{left:0;width:1200px;text-align:center;font-size:15px;line-height:26px;color:var(--text)}
.card{position:absolute;background:var(--white);border-radius:12px;box-shadow:0 3px 10px rgba(0,0,0,.12);overflow:hidden}
.card .photo{height:276px}
.card .label{text-align:center;font-family:'Lato',sans-serif;font-size:17px;color:var(--ink);padding-top:13px}
.arrow{position:absolute;width:32px;height:32px}

/* testimonials */
.quote-card{position:absolute;width:308px;height:244px;background:var(--white);border-radius:12px;box-shadow:0 3px 10px rgba(0,0,0,.12);padding:34px 24px 0}
.quote-mark{position:absolute;top:-24px;left:22px;font-family:'Montserrat',sans-serif;font-weight:700;font-size:64px;color:var(--blue);line-height:1}
.quote-card p{font-size:14px;line-height:26px;color:var(--text);height:78px;overflow:hidden}
.quote-card .more{font-size:14px;font-style:italic;text-decoration:underline;color:var(--text);margin-top:4px}
.person{display:flex;align-items:center;gap:20px;margin-top:14px}
.avatar{width:70px;height:70px;border-radius:50%;background:linear-gradient(135deg,#cfcac4,#8c8680)}
.person .who{font-size:18px;font-weight:700;color:var(--ink)}
.person .role{font-size:14px;color:var(--text);margin-top:4px}

/* cta */
.cta{left:111px;top:2361px;width:977px;height:346px;border-radius:173px;background:linear-gradient(120deg,#3f67e8,#2b52da 60%,#3760e4);color:var(--white);text-align:center}
.cta h2{font-family:'Montserrat',sans-serif;font-weight:700;font-size:40px;margin-top:74px}
.cta p{font-size:17px;margin-top:22px}
.cta .btn-light{display:inline-flex;margin-top:28px;width:216px;height:47px;align-items:center;justify-content:center;background:var(--white);color:var(--blue);border-radius:24px;font-size:17px}

/* work */
.tile{position:absolute;width:398px;height:347px}
.tile.hover{background:linear-gradient(135deg,#3d63e6,#2b4fd4);display:flex;align-items:center;justify-content:center;text-align:center;color:var(--white);font-family:'Montserrat',sans-serif;font-weight:700;font-size:26px;line-height:38px}

/* footer */
.footer{left:0;top:3710px;width:1200px;height:418px;background:var(--footer);color:#e2e2e2}
.footer .col-title{position:absolute;top:98px;font-family:'Lato',sans-serif;font-weight:700;font-size:20px;color:var(--white)}
.footer ul{position:absolute;top:140px;list-style:none;font-size:15px}
.footer ul li{height:34.4px;display:flex;align-items:center;gap:16px}
.footer ul li::before{content:"";width:7px;height:7px;border-radius:50%;background:#e2e2e2}
.footer .small li{font-size:13.5px}
.contact-line{position:absolute;left:886px;display:flex;gap:12px;font-size:15px;line-height:24px}
.contact-line svg{flex:none;margin-top:4px}
.divider{left:112px;top:354px;width:976px;height:1px;background:#666}
.copy{left:0;width:1200px;top:372px;text-align:center;font-size:14px}
</style>
</head>
<body>

<!-- header -->
<div class="abs topbar">
  <div class="item" style="left:36px">
    <svg width="18" height="18" viewBox="0 0 24 24" fill="none" stroke="#fff" stroke-width="2"><path d="M5 3h4l2 5-3 2a12 12 0 0 0 6 6l2-3 5 2v4a2 2 0 0 1-2 2A17 17 0 0 1 3 5a2 2 0 0 1 2-2z"/></svg>
    +44 (0) 7700 900418
  </div>
  <div class="item" style="left:284px">
    <svg width="18" height="14" viewBox="0 0 24 18" fill="none" stroke="#fff" stroke-width="2"><rect x="1" y="1" width="22" height="16" rx="2"/><path d="M1 2l11 8 11-8"/></svg>
    info@valtorix.design
  </div>
  <div class="item" style="left:535px;gap:16px">
    <span class="social-dot"></span><span class="social-dot"></span><span class="social-dot"></span><span class="social-dot"></span>
  </div>
</div>

<div class="abs brand" style="left:112px;top:14px">
  <span class="mark"></span><span class="name">Valtorix</span>
</div>

<nav class="abs nav"><span>Home</span><span>Portfolio</span><span>Our Services</span></nav>
<svg class="abs" style="left:896px;top:61px" width="22" height="22" viewBox="0 0 24 24" fill="none" stroke="#2b2b2b" stroke-width="2.2"><circle cx="10" cy="10" r="7"/><path d="M15 15l6 6"/></svg>
<div class="btn" style="left:942px;top:48px;width:144px;height:48px">Contact Us</div>

<!-- hero -->
<svg class="abs" style="left:0;top:112px" width="1200" height="630" viewBox="0 0 1200 630" role="img" aria-label="Photo of a laptop showing a CAD model of a mechanical part">
  <defs>
    <linearGradient id="heroFill" x1="0" y1="0" x2="1" y2="1">
      <stop offset="0" stop-color="#d6d9de"/>
      <stop offset=".45" stop-color="#8a939c"/>
      <stop offset="1" stop-color="#5b6670"/>
    </linearGradient>
  </defs>
  <path d="M0 0H1200V508Q600 760 0 508Z" fill="url(#heroFill)"/>
  <path d="M0 508Q600 760 1200 508" fill="none" stroke="#2f5be6" stroke-width="6"/>
</svg>
<h1 class="abs hero-title">Precision Mechanical Design<br>Engineered for Performance</h1>
<p class="abs hero-sub">From concept to production — expert CAD, engineering development, and manufacturable design solutions.</p>
<div class="btn" style="left:529px;top:610px;width:142px;height:47px">Get Started</div>

<!-- about -->
<svg class="abs" style="left:160px;top:802px" width="344" height="344" viewBox="0 0 344 344">
  <circle cx="172" cy="172" r="166" fill="none" stroke="#2f5be6" stroke-width="6" stroke-dasharray="560 600" transform="rotate(110 172 172)"/>
  <circle cx="176" cy="170" r="162" fill="#c9c2ba" role="img" aria-label="Portrait photo of the chief engineer"/>
</svg>
<h2 class="abs heading" style="left:644px;top:820px;font-size:40px"><span class="accent">About</span> Us</h2>
<p class="abs about-text">Rowan Hale is the Chief Engineer at Valtorix Mechanical Design. He has 11 years experience working as a mechanical design engineer in multiple industries including high performance automotive, consumer products, medical, industrial plus many more. He has worked in multiple roles across a wide range of products.</p>
<div class="btn" style="left:644px;top:1062px;width:146px;height:45px">Read More</div>

<!-- expertise -->
<div class="abs band"></div>
<h2 class="abs heading section-title" style="top:1294px"><span class="accent">Our</span> Expertise</h2>
<p class="abs intro" style="top:1368px">Welcome to Valtorix Mechanical Design. We are a UK based design consultancy offering a comprehensive mechanical and<br>product design service from initial concepts through to full volume production.</p>

<svg class="arrow" style="left:35px;top:1599px" viewBox="0 0 32 32" fill="none" stroke="#666" stroke-width="2"><circle cx="16" cy="16" r="14"/><path d="M23 16H10M15 11l-5 5 5 5"/></svg>
<svg class="arrow" style="left:1129px;top:1599px" viewBox="0 0 32 32" fill="none" stroke="#2f5be6" stroke-width="2"><circle cx="16" cy="16" r="14"/><path d="M9 16h13M17 11l5 5-5 5"/></svg>

<div class="card" style="left:112px;top:1451px;width:305px;height:326px">
  <div class="photo" role="img" aria-label="Photo of a CNC machine cutting a part" style="background:linear-gradient(135deg,#2a3540,#4d6b86 60%,#7fb4e0)"></div>
  <div class="label">Bespoke Product Design</div>
</div>
<div class="card" style="left:447px;top:1451px;width:304px;height:326px">
  <div class="photo" role="img" aria-label="Photo of an engineer viewing a 3D model on monitors" style="background:linear-gradient(135deg,#5c6167,#9aa0a6 55%,#3e4349)"></div>
  <div class="label">3D Modelling and Drawings</div>
</div>
<div class="card" style="left:782px;top:1451px;width:304px;height:326px">
  <div class="photo" role="img" aria-label="Photo of two engineers reviewing a tablet in a factory" style="background:linear-gradient(135deg,#a7c3dc,#6f8fae 55%,#c8d6e2)"></div>
  <div class="label">Design for Manufacture</div>
</div>

<!-- testimonials -->
<h2 class="abs heading section-title" style="top:1934px"><span class="accent">What Our</span> Clients Say</h2>

<svg class="arrow" style="left:35px;top:2131px" viewBox="0 0 32 32" fill="none" stroke="#666" stroke-width="2"><circle cx="16" cy="16" r="14"/><path d="M23 16H10M15 11l-5 5 5 5"/></svg>
<svg class="arrow" style="left:1129px;top:2131px" viewBox="0 0 32 32" fill="none" stroke="#2f5be6" stroke-width="2"><circle cx="16" cy="16" r="14"/><path d="M9 16h13M17 11l5 5-5 5"/></svg>

<div class="quote-card" style="left:112px;top:2031px">
  <span class="quote-mark">“</span>
  <p>I had the pleasure of working alongside Rowan on a day-to-day basis to deliver the most complex machined casting for</p>
  <div class="more">Read More</div>
  <div class="person"><span class="avatar" role="img" aria-label="Client portrait"></span><div><div class="who">Declan Marsh</div><div class="role">Project Manager</div></div></div>
</div>
<div class="quote-card" style="left:445px;top:2031px">
  <span class="quote-mark">“</span>
  <p>Rowan went above and beyond in all aspects of the job. He identified issues with the design that I had not foreseen,</p>
  <div class="more">Read More</div>
  <div class="person"><span class="avatar" role="img" aria-label="Client portrait" style="background:linear-gradient(135deg,#8a8580,#3a3633)"></span><div><div class="who">Ellis</div><div class="role">Manager</div></div></div>
</div>
<div class="quote-card" style="left:780px;top:2031px">
  <span class="quote-mark">“</span>
  <p>Rowan is able to bridge the gap between what management want and what manufacturing can deliver. In the</p>
  <div class="more">Read More</div>
  <div class="person"><span class="avatar" role="img" aria-label="Client portrait" style="background:linear-gradient(135deg,#f0a040,#d7742a)"></span><div><div class="who">Tobias Wren</div><div class="role">Design Engineer</div></div></div>
</div>

<!-- cta -->
<div class="abs cta" role="img" aria-label="Blue panel over a faint CAD software background">
  <h2>Curious What Else We Do?</h2>
  <p>We support projects at every stage — from early idea development through manufacturing and beyond.</p>
  <span class="btn-light">Book a Consultation</span>
</div>

<!-- work -->
<h2 class="abs heading section-title" style="top:2780px"><span class="accent">Our</span> Work</h2>
<p class="abs intro" style="top:2848px">A small selection of our previous projects</p>

<div class="tile" style="left:0;top:2908px;background:linear-gradient(135deg,#f1f1f1,#d4d4d4)" role="img" aria-label="Render of a driving simulator rig"></div>
<div class="tile" style="left:401px;top:2908px;background:linear-gradient(135deg,#eeeeee,#c9c9c9)" role="img" aria-label="Render of a camera mount on a threaded rod"></div>
<div class="tile" style="left:801px;top:2908px;width:399px;background:linear-gradient(135deg,#fafafa,#d8d8d8)" role="img" aria-label="Render of a polished alloy wheel"></div>
<div class="tile" style="left:0;top:3260px;background:linear-gradient(135deg,#2a211b,#6b4a30 60%,#1a1a1a)" role="img" aria-label="Photo of a pen on a wooden stand"></div>
<div class="tile hover" style="left:401px;top:3260px" role="img" aria-label="Transmission assembly project with blue overlay">High-Performance<br>Transmission Assembly</div>
<div class="tile" style="left:801px;top:3260px;width:399px;background:linear-gradient(135deg,#f5f5f5,#d8dde0)" role="img" aria-label="Render of an industrial press machine"></div>

<!-- footer -->
<footer class="abs footer">
  <div class="abs brand" style="left:112px;top:84px">
    <span class="mark" style="width:68px;height:68px;border-color:#fff;border-width:11px"></span><span class="name" style="color:#fff;font-size:34px">Valtorix</span>
  </div>
  <div class="abs" style="left:118px;top:215px;display:flex;gap:16px;color:#fff">
    <span class="social-dot"></span><span class="social-dot"></span><span class="social-dot"></span><span class="social-dot"></span>
  </div>

  <div class="col-title" style="left:409px">Quick Links</div>
  <ul style="left:412px"><li>Home</li><li>Portfolio</li><li>Services</li><li>About</li><li>Testimonials</li><li>FAQ</li></ul>

  <div class="col-title" style="left:578px">Capabilities</div>
  <ul class="small" style="left:580px"><li>Mechanical CAD Design</li><li>Product Development</li><li>3D Modelling / Engineering Drawings</li><li>Design for Manufacture (DFM)</li><li>Prototype Support</li><li>Supplier &amp; Manufacturing Liaison</li></ul>

  <div class="col-title" style="left:886px">Contact Us</div>
  <div class="contact-line" style="top:142px">
    <svg width="16" height="18" viewBox="0 0 16 20" fill="#fff"><path d="M8 0a7 7 0 0 0-7 7c0 5 7 13 7 13s7-8 7-13a7 7 0 0 0-7-7zm0 10a3 3 0 1 1 0-6 3 3 0 0 1 0 6z"/></svg>
    <span>22 Larch Street, 58 W 9th St,<br>New York, NY 10012,</span>
  </div>
  <div class="contact-line" style="top:204px">
    <svg width="16" height="16" viewBox="0 0 16 16"><circle cx="8" cy="8" r="8" fill="#fff"/><rect x="4" y="5" width="8" height="6" fill="none" stroke="#3b3b3b" stroke-width="1.2"/><path d="M4 5l4 3 4-3" fill="none" stroke="#3b3b3b" stroke-width="1.2"/></svg>
    <span>info@valtorix.design</span>
  </div>
  <div class="contact-line" style="top:248px">
    <svg width="16" height="16" viewBox="0 0 16 16"><circle cx="8" cy="8" r="8" fill="#fff"/><path d="M5 4h2l1 2-1.5 1a5 5 0 0 0 2.5 2.5L10 8l2 1v2a1 1 0 0 1-1 1A7 7 0 0 1 4 5a1 1 0 0 1 1-1z" fill="#3b3b3b"/></svg>
    <span>+44 (0) 7700 900418</span>
  </div>

  <div class="abs divider"></div>
  <p class="abs copy">© 2025 Valtorix Mechanical Design — All Rights Reserved.</p>
</footer>

</body>
</html>
```